Business card for a new cabinet shop company named Veloran Cabinets for high end cabinets

Design a business card, thinking dark rich green with colours to speak of high end luxury ie; cream, gold, black possibly

Mitchell Tarrowby
Director Craftsman
Email: info@veloranjoinery-example.com.au
Instagram : @veloran.cabinets

```html
<!DOCTYPE html>
<html lang="en">
<head>
<meta charset="utf-8">
<title>Veloran Cabinets – Business Card</title>
<link href="https://fonts.googleapis.com/css2?family=Josefin+Sans:wght@300;400&display=swap" rel="stylesheet">
<style>
  :root {
    --backdrop: #d6d6d4;
    --card: #ffffff;
    --ink: #1d1a1b;
    --ink-warm: #3a3227;
    --gold: #b89a52;
    --muted: #6f6f6f;
    --rule: #9a9a9a;
  }
  * { margin: 0; padding: 0; box-sizing: border-box; }
  html, body { width: 1200px; height: 900px; overflow: hidden; }
  body {
    background: var(--backdrop);
    font-family: "Josefin Sans", sans-serif;
    position: relative;
  }
  .card {
    position: absolute;
    left: 260px;
    width: 680px;
    height: 389px;
    background: var(--card);
    overflow: hidden;
    box-shadow: 0 6px 18px rgba(0,0,0,0.18);
  }
  .card--front { top: 40px; }
  .card--back { top: 471px; }

  .feature-panel {
    position: absolute;
    top: 0;
    width: 240px;
    height: 389px;
    background: linear-gradient(160deg, var(--ink) 0%, var(--ink) 55%, var(--ink-warm) 100%);
  }
  .card--front .feature-panel { left: 0; }
  .card--back .feature-panel { right: 0; }

  .wordmark {
    position: absolute;
    color: var(--gold);
    font-weight: 400;
    line-height: 1;
  }
  .wordmark__main { display: block; }
  .wordmark__sub { display: block; text-transform: uppercase; letter-spacing: 0.42em; }

  .card--front .wordmark { left: 330px; top: 120px; }
  .card--front .wordmark__main { font-size: 86px; }
  .card--front .wordmark__sub { font-size: 34px; margin-top: 10px; }

  .contact {
    position: absolute;
    left: 118px;
    top: 88px;
    width: 300px;
  }
  .contact__name {
    color: var(--gold);
    font-size: 20px;
    font-weight: 400;
    text-transform: uppercase;
    letter-spacing: 0.02em;
  }
  .contact__role {
    color: var(--muted);
    font-size: 16px;
    font-weight: 300;
    margin-top: 6px;
  }
  .contact__rule {
    border: 0;
    border-top: 1px solid var(--rule);
    margin: 14px 0 12px;
  }
  .contact__list { list-style: none; }
  .contact__item {
    display: flex;
    align-items: center;
    gap: 8px;
    color: var(--muted);
    font-size: 15px;
    font-weight: 300;
    margin-bottom: 6px;
    white-space: nowrap;
  }
  .contact__icon { width: 14px; height: 14px; flex: none; }

  .card--back .wordmark { left: 118px; top: 262px; }
  .card--back .wordmark__main { font-size: 60px; }
  .card--back .wordmark__sub { font-size: 24px; margin-top: 6px; }
</style>
</head>
<body>

<section class="card card--front" aria-label="Card front">
  <div class="feature-panel" role="img" aria-label="Decorative black and gold stripe graphic"></div>
  <div class="wordmark">
    <span class="wordmark__main">Veloran</span>
    <span class="wordmark__sub">Cabinets</span>
  </div>
</section>

<section class="card card--back" aria-label="Card back">
  <div class="feature-panel" role="img" aria-label="Decorative black and gold stripe graphic"></div>
  <div class="contact">
    <p class="contact__name">Mitchell Tarrowby</p>
    <p class="contact__role">Director Craftsman</p>
    <hr class="contact__rule">
    <ul class="contact__list">
      <li class="contact__item">
        <svg class="contact__icon" viewBox="0 0 14 14" aria-hidden="true"><circle cx="7" cy="7" r="7" fill="#b89a52"/></svg>
        @veloran.cabinets
      </li>
      <li class="contact__item">
        <svg class="contact__icon" viewBox="0 0 14 14" aria-hidden="true">
          <rect x="0.5" y="2.5" width="13" height="9" fill="#b89a52"/>
          <polyline points="0.5,2.5 7,8 13.5,2.5" fill="none" stroke="#ffffff" stroke-width="1.2"/>
        </svg>
        info@veloranjoinery-example.com.au
      </li>
    </ul>
    <hr class="contact__rule">
  </div>
  <div class="wordmark">
    <span class="wordmark__main">Veloran</span>
    <span class="wordmark__sub">Cabinets</span>
  </div>
</section>

</body>
</html>
```